Business Card - high end, modern health care

Hey designers!

We need a double sided business card for the boutique, cutting edge physical therapy rehabilitation centre in Sydney's Northern Beaches.

With the most qualified physios in the area The Harbourview Motion Clinic does what other physiotherapy practices do not, we take our time with our patients giving them longer appointments, better physios and therefor faster results!

We guarantee that the service people receive at THMC will be unparalleled.

Hence we need a business card to reflect our modern, boutique, high end service. The final design needs to reflect that we are in a class of our own yet with the feel of beachside retreat.

Below I have attached our logo in both blue on white and white on blue. The exact colour is;
and the font that we have used in our logo is Tex Gyre Aventador.

I like the idea of the blue as the main colour as it is more eye catching and our signage onto the main road will be in this blue and in the interest of consistency across marketing the blue needs to be a part of the design. However I would appreciate a few designs onto a wooden background as this is a visual theme within the fitout of the practice.

The design needs to be of standard size (91x55mm).

Target Market(s)

We target people who have an end outcome in mind and those who have had poor experiences with other providers and ensure that everyone gets the care that they deserve with a premium service that is tailored to the individuals circumstances. As a premium service, the target market is highly educated, business and tech savvy with the additional target market of elderly people who have self funded their retirement and see value in paying for the best ongoing rehabilitation to maintain independence.

Industry/Entity Type

Physical Therapy

Contact Information for Business Card

Name, designation( Titled Musculoskeletal Physiotherapist... there will also be those in the company that have multiple designations ie 5 or 6 words long), phone number, email, facebook, instagram, address

Font styles to use
Sans Serif

Colors

Designer to choose colors to be used in the design.

Requirements
Must have
• Front - The logo as large as possible, blue or wooden theme, and all of the important details.
• Back - A blank space/lines on which to write appointment times (no "Appointment, date, time" etc.)
Nice to have
• facebook url
• logos for facebook and instagram
• Mini logos for the phone and email?

```html
<!DOCTYPE html>
<html lang="en">
<head>
<meta charset="utf-8">
<title>The Harbourview Motion Clinic – Business Card</title>
<link rel="stylesheet" href="https://fonts.googleapis.com/css2?family=Montserrat:wght@500;700&family=Roboto:wght@400;500&display=swap">
<style>
  :root{
    --brand-blue:#1458b0;
    --brand-blue-dark:#0c4593;
    --ink:#4a4a4a;
    --rule:#7a7a7a;
    --paper:#ffffff;
    --backdrop:#e9e6e1;
  }
  *{box-sizing:border-box;margin:0;padding:0}
  html,body{width:1200px;height:911px;overflow:hidden;background:var(--backdrop)}
  .canvas{position:relative;width:1200px;height:911px;display:flex;align-items:center;justify-content:center;gap:60px}
  .card{position:relative;width:520px;height:314px;background:var(--paper);border-radius:16px;overflow:hidden;box-shadow:0 10px 26px rgba(0,0,0,.18)}

  /* front */
  .side-band{position:absolute;left:0;top:0;bottom:0;width:64px;background:var(--brand-blue)}
  .brand-mark{position:absolute;left:28px;top:48px;width:68px;height:68px;border-radius:50%;background:var(--brand-blue);border:4px solid var(--paper)}
  .brand-name{position:absolute;left:108px;top:62px;color:var(--brand-blue);font-family:"Montserrat",sans-serif;font-weight:700;line-height:1;white-space:nowrap}
  .brand-name .line-1{display:block;font-size:22px;letter-spacing:-.4px}
  .brand-name .line-2{display:block;font-size:11px;letter-spacing:5px;margin-top:6px}
  .holder{position:absolute;right:26px;top:26px;text-align:right;font-family:"Roboto",sans-serif;white-space:nowrap}
  .holder-name{color:var(--brand-blue);font-weight:500;font-size:16px;letter-spacing:-.2px}
  .holder-title{color:var(--ink);font-size:12px;margin-top:3px}
  .divider{position:absolute;left:290px;right:26px;top:136px;height:1.5px;background:var(--brand-blue)}
  .contact-list{position:absolute;left:98px;top:150px;list-style:none;font-family:"Roboto",sans-serif;font-size:12px;color:var(--ink);line-height:18px;white-space:nowrap}
  .contact-list li.gap{margin-top:10px}
  .icons{position:absolute;left:0;top:150px;width:64px}
  .icons svg{position:absolute;left:25px;width:13px;height:13px;fill:var(--paper)}

  /* back */
  .back-brand{position:absolute;left:40px;top:36px;display:flex;align-items:center;gap:12px}
  .back-brand .dot{width:46px;height:46px;border-radius:50%;background:var(--brand-blue)}
  .back-brand .brand-text{color:var(--brand-blue);font-family:"Montserrat",sans-serif;font-weight:700;line-height:1;white-space:nowrap}
  .back-brand .line-1{display:block;font-size:22px;letter-spacing:-.4px}
  .back-brand .line-2{display:block;font-size:11px;letter-spacing:5px;margin-top:6px}
  .field-row{position:absolute;left:40px;right:40px;display:flex;align-items:flex-end;gap:6px;font-family:"Roboto",sans-serif;font-size:13px;color:var(--ink)}
  .field-row .blank{flex:1;border-bottom:1px solid var(--rule);height:1px}
  .write-line{position:absolute;left:40px;right:40px;height:1px;background:var(--rule)}
</style>
</head>
<body>
<main class="canvas">

  <section class="card card-front" aria-label="Card front">
    <div class="side-band"></div>
    <div class="brand-mark"></div>
    <h1 class="brand-name"><span class="line-1">THE HARBOURVIEW</span><span class="line-2">MOTION CLINIC</span></h1>

    <div class="holder">
      <p class="holder-name">MARA ELLISON</p>
      <p class="holder-title">CEO/FOUNDER</p>
    </div>
    <div class="divider"></div>

    <div class="icons" aria-hidden="true">
      <svg viewBox="0 0 24 24" style="top:2px"><path d="M12 2a7 7 0 0 0-7 7c0 5 7 13 7 13s7-8 7-13a7 7 0 0 0-7-7zm0 9.5A2.5 2.5 0 1 1 12 6.5a2.5 2.5 0 0 1 0 5z"/></svg>
      <svg viewBox="0 0 24 24" style="top:48px"><path d="M6.6 10.8a15 15 0 0 0 6.6 6.6l2.2-2.2a1 1 0 0 1 1-.25 11.4 11.4 0 0 0 3.6.57 1 1 0 0 1 1 1V20a1 1 0 0 1-1 1A17 17 0 0 1 3 4a1 1 0 0 1 1-1h3.5a1 1 0 0 1 1 1c0 1.25.2 2.45.57 3.57a1 1 0 0 1-.25 1z"/></svg>
      <svg viewBox="0 0 24 24" style="top:66px"><path d="M3 5h18v14H3zm2 2v.5l7 4.5 7-4.5V7z"/></svg>
      <svg viewBox="0 0 24 24" style="top:84px"><circle cx="12" cy="12" r="10"/></svg>
      <svg viewBox="0 0 24 24" style="top:102px"><rect x="3" y="3" width="18" height="18" rx="3"/></svg>
      <svg viewBox="0 0 24 24" style="top:120px"><rect x="3" y="3" width="18" height="18" rx="5"/></svg>
    </div>

    <ul class="contact-list">
      <li>42 Tidewater Lane</li>
      <li>Northport, Coastal 20418</li>
      <li class="gap">610 555 0184</li>
      <li>mara@harbourviewmotion.com</li>
      <li>www.harbourviewmotion.com</li>
      <li>/harbourviewmotion</li>
      <li>@harbourviewmotion</li>
    </ul>
  </section>

  <section class="card card-back" aria-label="Card back">
    <div class="back-brand">
      <div class="dot"></div>
      <p class="brand-text"><span class="line-1">THE HARBOURVIEW</span><span class="line-2">MOTION CLINIC</span></p>
    </div>

    <div class="field-row" style="top:112px"><span>Name</span><span class="blank"></span></div>
    <div class="field-row" style="top:146px"><span>Date</span><span class="blank"></span><span>Time</span><span class="blank"></span><span>am/pm</span></div>
    <div class="write-line" style="top:196px"></div>
    <div class="write-line" style="top:226px"></div>
    <div class="write-line" style="top:256px"></div>
    <div class="write-line" style="top:286px"></div>
  </section>

</main>
</body>
</html>
```